High-end construction company needs a business card design

We need a modern looking business card that draws people in, is memorable and looks so good people will want to sick it on their fridges.
On the first side what is needed are:
Logo
My name - Tomasz Brelwik
Title - Managing Director
Website - www.varkelt.co.uk
Email - tomasz@varkelt.co.uk
Telephone - 020 5194 6281
Mobile - 07845139072
On the back side was is needed is a list of all the services we provide:
-Kitchen Renovations
-Bathroom Renovations
-House Renovations
-Garage Conversions
-Extensions
-Loft Conversions
-Conservatories
-Carpentry
-Tiling
-Electrical
-Plumbing & Heating
-Bricklaying
-Landscaping
-Decorating
-Plastering
We would like the colours to be the same shades as on the logo with grey or black for the words.
Target Market(s)
Anyone who needs building work done
Contact Information for Business Card
This business card is for a construction company which strives to deliver excellent service and quality.
The look and feel of the card should represent this.
Requirements
Must have
- On the first side what is needed are:
Logo
My name - Tomasz Brelwik
Title - Managing Director
Website - www.varkelt.co.uk
Email - tomasz@varkelt.co.uk
Telephone - 020 5194 6281
Mobile - 07845139072
Nice to have
- Cool looking features

```html
<!DOCTYPE html>
<html lang="en">
<head>
<meta charset="utf-8">
<title>Varkelt Construction Ltd – Business Card</title>
<link rel="stylesheet" href="https://fonts.googleapis.com/css2?family=Didact+Gothic&family=Montserrat:wght@700&display=swap">
<style>
  :root {
    --stage: #2f3032;
    --card: #ffffff;
    --card-shade: #ececec;
    --green: #4caf3a;
    --green-dark: #2f8a2c;
    --text-grey: #4d4d4d;
    --rule-grey: #b9b9b9;
    --deco-grey: #e3e3e3;
  }
  * { box-sizing: border-box; margin: 0; padding: 0; }
  html, body { width: 1200px; height: 900px; overflow: hidden; }
  body {
    background: var(--stage);
    position: relative;
    font-family: "Didact Gothic", "Century Gothic", sans-serif;
    color: var(--text-grey);
  }

  .card {
    position: absolute;
    width: 700px;
    height: 400px;
    border-radius: 38px;
    background: linear-gradient(135deg, var(--card) 0%, #f7f7f7 55%, var(--card-shade) 100%);
    overflow: hidden;
  }
  .card--services { left: 70px; top: 40px; }
  .card--front { left: 430px; top: 460px; }

  .card__decoration {
    position: absolute;
    right: 40px;
    top: 30px;
    width: 340px;
    height: 340px;
    border-radius: 20px;
    background: radial-gradient(circle at 55% 45%, var(--deco-grey) 0%, rgba(227,227,227,0.4) 55%, rgba(227,227,227,0) 75%);
  }

  /* Wordmark */
  .wordmark {
    position: absolute;
    display: flex;
    align-items: center;
    gap: 12px;
    font-family: "Montserrat", sans-serif;
    font-weight: 700;
    color: var(--green);
    text-transform: uppercase;
    line-height: 1.05;
  }
  .wordmark__square {
    flex: none;
    background: var(--green);
  }
  .card--services .wordmark { left: 262px; top: 168px; font-size: 22px; }
  .card--services .wordmark__square { width: 26px; height: 26px; }
  .card--front .wordmark { left: 60px; top: 130px; font-size: 40px; }
  .card--front .wordmark__square { width: 48px; height: 48px; }
  .wordmark__sub { display: block; font-size: 0.42em; letter-spacing: 0.12em; }

  /* Services side */
  .services__title {
    position: absolute;
    left: 262px;
    top: 60px;
    font-family: "Montserrat", sans-serif;
    font-weight: 700;
    font-size: 22px;
    color: var(--green);
    letter-spacing: 0.02em;
  }
  .services__list {
    position: absolute;
    list-style: none;
    font-size: 18px;
    line-height: 38px;
  }
  .services__list--left { left: 50px; top: 96px; }
  .services__list--right { right: 50px; top: 38px; text-align: right; }
  .services__item { display: flex; align-items: center; gap: 10px; }
  .services__list--right .services__item { justify-content: flex-end; }
  .services__bullet {
    width: 11px; height: 11px;
    background: var(--green);
    flex: none;
  }

  /* Front side */
  .person {
    position: absolute;
    left: 330px;
    top: 270px;
  }
  .person__title { font-size: 22px; color: var(--text-grey); }
  .person__name {
    font-family: "Montserrat", sans-serif;
    font-weight: 700;
    font-size: 27px;
    color: var(--green);
    text-transform: uppercase;
    margin-top: 2px;
  }
  .contact {
    position: absolute;
    left: 430px;
    top: 90px;
    padding-left: 22px;
    border-left: 1.5px solid var(--rule-grey);
    list-style: none;
    font-size: 20px;
    line-height: 38px;
  }
  .contact__item { display: flex; align-items: center; gap: 12px; }
  .contact__icon { width: 18px; height: 18px; flex: none; fill: var(--green); }
</style>
</head>
<body>

  <section class="card card--services" aria-label="Services side">
    <div class="card__decoration" role="img" aria-label="Faint grey illustration of an excavator arm over a building"></div>

    <h2 class="services__title">SERVICES</h2>

    <ul class="services__list services__list--left">
      <li class="services__item"><span class="services__bullet"></span>Kitchen Renovations</li>
      <li class="services__item"><span class="services__bullet"></span>Bathroom Renovations</li>
      <li class="services__item"><span class="services__bullet"></span>House Renovations</li>
      <li class="services__item"><span class="services__bullet"></span>Garage Conversions</li>
      <li class="services__item"><span class="services__bullet"></span>Extensions</li>
      <li class="services__item"><span class="services__bullet"></span>Loft Conversions</li>
      <li class="services__item"><span class="services__bullet"></span>Conservatories | Carpentry</li>
    </ul>

    <div class="wordmark">
      <span class="wordmark__square"></span>
      <span>Varkelt<span class="wordmark__sub">Construction Ltd</span></span>
    </div>

    <ul class="services__list services__list--right">
      <li class="services__item">Tiling<span class="services__bullet"></span></li>
      <li class="services__item">Electrical<span class="services__bullet"></span></li>
      <li class="services__item">Plumbing &amp; Heating<span class="services__bullet"></span></li>
      <li class="services__item">Bricklaying<span class="services__bullet"></span></li>
      <li class="services__item">Landscaping<span class="services__bullet"></span></li>
      <li class="services__item">Decorating<span class="services__bullet"></span></li>
      <li class="services__item">Plastering services<span class="services__bullet"></span></li>
    </ul>
  </section>

  <section class="card card--front" aria-label="Contact side">
    <div class="card__decoration" role="img" aria-label="Faint grey illustration of an excavator arm over a building"></div>

    <div class="wordmark">
      <span class="wordmark__square"></span>
      <span>Varkelt<span class="wordmark__sub">Construction Ltd</span></span>
    </div>

    <div class="person">
      <p class="person__title">Managing Director</p>
      <p class="person__name">Tomasz Brelwik</p>
    </div>

    <ul class="contact">
      <li class="contact__item">
        <svg class="contact__icon" viewBox="0 0 18 18" aria-hidden="true"><rect x="4" y="1" width="10" height="16" rx="2" fill="none" stroke="#4caf3a" stroke-width="2"/><circle cx="9" cy="14" r="1"/></svg>
        07845139072
      </li>
      <li class="contact__item">
        <svg class="contact__icon" viewBox="0 0 18 18" aria-hidden="true"><path d="M2 6c0-2 3-3 7-3s7 1 7 3v1h-4V5.5H6V7H2z"/><rect x="3" y="9" width="12" height="7" rx="1.5"/></svg>
        020 5194 6281
      </li>
      <li class="contact__item">
        <svg class="contact__icon" viewBox="0 0 18 18" aria-hidden="true"><rect x="1" y="4" width="16" height="11" rx="1.5"/><path d="M1.5 5l7.5 5.5L16.5 5" fill="none" stroke="#fff" stroke-width="1.5"/></svg>
        tomasz@varkelt.co.uk
      </li>
      <li class="contact__item">
        <svg class="contact__icon" viewBox="0 0 18 18" aria-hidden="true"><circle cx="9" cy="9" r="8"/><path d="M1 9h16M9 1c-3 3-3 13 0 16M9 1c3 3 3 13 0 16" fill="none" stroke="#fff" stroke-width="1.2"/></svg>
        www.varkelt.co.uk
      </li>
    </ul>
  </section>

</body>
</html>
```